Realty Group Needs Classy, Contemporary Letterhead Design

We need a letterhead design for a new realty company located in NY, USA. We buy investment properties to rehabilitate and or keep in our rental portfolio.

```html
<!DOCTYPE html>
<html lang="en">
<head>
<meta charset="utf-8">
<title>Halvern Realty Group Letterhead</title>
<link href="https://fonts.googleapis.com/css2?family=Open+Sans:wght@400;600;700;800&display=swap" rel="stylesheet">
<style>
  :root {
    --backdrop: #ececec;
    --paper: #ffffff;
    --brand-purple: #4b2a94;
    --brand-purple-dark: #35206b;
    --ink-grey: #6f6f73;
    --rule-grey: #b9b9bd;
  }
  * { margin: 0; padding: 0; box-sizing: border-box; }
  html, body {
    width: 1200px;
    height: 795px;
    overflow: hidden;
    background: var(--backdrop);
    font-family: "Open Sans", Arial, sans-serif;
  }
  .letterhead {
    position: absolute;
    left: 338px;
    top: 28px;
    width: 524px;
    height: 740px;
    background: var(--paper);
    box-shadow: 0 2px 10px rgba(0,0,0,0.08);
  }
  .edge-tab {
    position: absolute;
    left: 0;
    top: 58px;
    width: 44px;
    height: 40px;
  }
  .brand {
    position: absolute;
    left: 52px;
    top: 54px;
    color: var(--brand-purple);
    font-weight: 800;
    line-height: 1;
  }
  .brand-name {
    display: block;
    font-size: 26px;
    letter-spacing: 0.5px;
  }
  .brand-sub {
    display: block;
    margin-top: 3px;
    font-size: 9px;
    letter-spacing: 1px;
    padding-left: 22px;
  }
  .contact-list {
    position: absolute;
    right: 44px;
    top: 32px;
    list-style: none;
    font-size: 7.5px;
    line-height: 11px;
    color: var(--ink-grey);
  }
  .contact-list li {
    display: flex;
    align-items: center;
    gap: 5px;
  }
  .contact-icon {
    width: 8px;
    height: 8px;
    background: var(--brand-purple);
    flex: none;
  }
  .footer {
    position: absolute;
    left: 40px;
    right: 40px;
    bottom: 44px;
    height: 60px;
  }
  .footer-rule {
    position: absolute;
    left: 0;
    right: 0;
    bottom: 14px;
    height: 1px;
    background: var(--rule-grey);
  }
  .footer-band {
    position: absolute;
    right: 0;
    bottom: 10px;
    width: 188px;
    height: 9px;
    background: var(--brand-purple);
  }
  .footer-address {
    position: absolute;
    right: 0;
    bottom: 24px;
    text-align: right;
    line-height: 13px;
  }
  .footer-company {
    display: block;
    font-size: 10px;
    font-weight: 700;
    color: var(--brand-purple);
  }
  .footer-street {
    display: block;
    font-size: 10px;
    color: var(--ink-grey);
  }
</style>
</head>
<body>
  <main class="letterhead">
    <svg class="edge-tab" viewBox="0 0 44 40" aria-hidden="true">
      <polygon points="0,0 30,0 44,20 30,40 0,40" fill="var(--brand-purple)"/>
      <polygon points="0,40 10,40 0,48" fill="var(--brand-purple-dark)"/>
    </svg>

    <div class="brand">
      <span class="brand-name">HALVERN</span>
      <span class="brand-sub">Realty Group, LLC</span>
    </div>

    <ul class="contact-list">
      <li><span class="contact-icon"></span>(00) 0123 567 890</li>
      <li><span class="contact-icon"></span>(00) 0123 567 891</li>
      <li><span class="contact-icon"></span>info@halvernrealtygroup.com</li>
      <li><span class="contact-icon"></span>www.halvernrealtygroup.com</li>
    </ul>

    <footer class="footer">
      <div class="footer-address">
        <span class="footer-company">Halvern Realty Group, LLC</span>
        <span class="footer-street">Suite 102 Street Name, State, Zip 2034, Country</span>
      </div>
      <div class="footer-rule"></div>
      <div class="footer-band"></div>
    </footer>
  </main>
</body>
</html>
```